BRIGHTHOLD PROPERTY MANAGEMENT INC. WEBSITE

Please make the website more family-friendly.

I want a website to help me build my property management business by adding listing properties and creating an online application. Im open to any other ideas.
I want a WordPress designer to code it.

Here is my current website. www.brighthold.biz

IDEA: I like the website design https://www.pelicanclimateservices.com/

Thank you

Tom

Number of Pages Required

5+ page

```html
<!DOCTYPE html>
<html lang="en">
<head>
<meta charset="utf-8">
<title>Brighthold Property Management</title>
<link rel="stylesheet" href="https://fonts.googleapis.com/css2?family=Noto+Serif:wght@400;700&family=Roboto+Slab:wght@700&display=swap">
<style>
:root{
  --red:#a40f16;
  --red-dark:#86090f;
  --ink:#1d1d1d;
  --text:#333;
  --muted:#777;
  --line:#d9d9d9;
  --field:#ececec;
  --white:#fff;
  --navy:#1a1e29;
  --foot:#f1f1f1;
}
*{box-sizing:border-box;margin:0;padding:0}
html,body{width:1200px;height:4034px;overflow:hidden;background:var(--white)}
body{position:relative;font-family:"Noto Serif",serif;color:var(--text)}
.abs{position:absolute}
.btn{position:absolute;background:var(--red);color:var(--white);font-family:"Noto Serif",serif;font-size:15px;border-radius:6px;display:flex;align-items:center;justify-content:center;gap:8px}

/* header */
.brand{position:absolute;display:flex;flex-direction:column;align-items:center;color:var(--red);font-family:"Noto Serif",serif}
.brand-mark{width:42px;height:42px;border-radius:50%;background:var(--red)}
.brand-name{font-size:28px;letter-spacing:1px;margin-top:14px}
.search{left:340px;top:20px;width:354px;height:50px;background:var(--field);border-radius:6px;font-size:12px;padding:16px 24px;color:#444}
.search svg{position:absolute;right:22px;top:16px}
.main-nav{left:388px;top:100px;display:flex;gap:34px;font-size:14px;color:#222}
.main-nav span::after{content:"";display:inline-block;margin-left:6px;border:5px solid transparent;border-top:6px solid #222;border-bottom:0;vertical-align:middle}

/* hero */
.hero-photo{left:0;top:150px;width:1200px;height:690px;background:linear-gradient(100deg,#4a4436 0%,#8a806c 30%,#cfc8bb 55%,#e8e4de 80%,#b9b2a6 100%)}
.hero-copy{left:108px;top:282px;color:var(--white);font-family:"Roboto Slab",serif;text-shadow:0 2px 4px rgba(0,0,0,.4)}
.hero-copy h1{font-size:47px;letter-spacing:4px;line-height:1}
.hero-copy p{font-size:34px;letter-spacing:3px;line-height:42px;margin:20px 0 0 6px}
.hero-copy em{font-style:normal;color:var(--red)}

/* section titles */
.section-title{position:absolute;left:0;width:1200px;display:flex;justify-content:center;align-items:center;gap:14px;font-family:"Roboto Slab",serif;font-size:44px;color:var(--ink)}
.section-title::before{content:"";width:68px;height:4px;background:linear-gradient(90deg,transparent,var(--red));border-radius:2px}
.section-title.light{color:var(--white)}
.section-title.light::before{background:linear-gradient(90deg,transparent,var(--white))}

.about-text{left:160px;width:880px;top:948px;text-align:center;font-size:13.5px;line-height:29px;letter-spacing:.6px;color:#333}
.about-text p+p{margin-top:8px}

/* manager */
.manager{left:0;top:1275px;width:1200px;height:563px}
.manager-copy{left:115px;top:1330px;width:460px;color:var(--white)}
.manager-copy h2{font-family:"Roboto Slab",serif;font-size:44px;line-height:60px;font-weight:700}
.manager-copy h2 .dash{display:inline-block;width:70px;height:4px;background:var(--white);vertical-align:middle;margin-right:12px;border-radius:2px}
.manager-copy p{font-size:13px;line-height:27px;margin-top:22px}

/* listings */
.card{position:absolute;top:2025px;width:316px;height:420px;background:var(--white);box-shadow:0 0 10px rgba(0,0,0,.18)}
.card .ph{position:absolute;left:13px;top:13px;width:290px;height:210px}
.card h3{position:absolute;left:14px;top:242px;width:290px;font-size:19px;line-height:27px;color:var(--ink);font-weight:700}
.card .price{position:absolute;left:18px;font-size:16px;color:var(--red)}
.card .status{position:absolute;font-size:16px;color:var(--red)}
.card .specs{position:absolute;left:16px;right:16px;top:362px;border-top:1px solid var(--line);padding-top:20px;display:flex;align-items:center;font-size:12px;color:#333;gap:10px}
.rented{position:absolute;left:680px;top:2005px;width:78px;height:70px;background:var(--red);color:var(--white);font-size:16px;display:flex;align-items:center;justify-content:center}
.pager{position:absolute;top:2256px;width:24px;height:24px;border-radius:50%;background:#bbb}

/* applicants */
.applicants{left:0;top:2530px;width:1200px;height:536px;background:linear-gradient(180deg,#2b2e38 0%,#22242b 55%,#35302a 100%)}
.feature{position:absolute;top:2758px;width:200px;text-align:center;color:var(--white);font-family:"Roboto Slab",serif;font-size:20px}
.feature svg{display:block;margin:0 auto 18px}

/* form */
.field{position:absolute;height:52px;border:1px solid var(--line);font-size:13px;color:#333;padding:18px 16px}
.field .chev{position:absolute;right:18px;top:18px}

/* footer */
.footer-bg{left:0;top:3600px;width:1200px;height:434px}
.foot-links{left:0;width:1200px;top:3922px;display:flex;justify-content:center;font-size:15px;color:#222}
.foot-links span+span::before{content:"|";color:var(--red);margin:0 14px;font-weight:700}
.copyright{left:424px;top:3997px;font-size:11px;color:#222}
.socials{left:917px;top:3992px;display:flex;gap:6px}
.socials i{width:22px;height:22px;background:var(--red);border-radius:3px;display:block}
</style>
</head>
<body>

<!-- header -->
<div class="brand" style="left:110px;top:14px;width:200px">
  <span class="brand-mark"></span>
  <span class="brand-name">BRIGHTHOLD</span>
</div>
<div class="abs search">Search
  <svg width="18" height="18" viewBox="0 0 18 18"><circle cx="7.5" cy="7.5" r="6" fill="none" stroke="#333" stroke-width="1.6"/><path d="M12 12l5 5" stroke="#333" stroke-width="1.6"/></svg>
</div>
<div class="btn" style="left:732px;top:20px;width:111px;height:40px">
  <svg width="16" height="14" viewBox="0 0 16 14"><path d="M8 0L0 7h2v7h4V9h4v5h4V7h2z" fill="#fff"/></svg>Home</div>
<div class="btn" style="left:853px;top:20px;width:112px;height:40px">
  <svg width="18" height="12" viewBox="0 0 18 12"><rect x="0.5" y="0.5" width="17" height="11" fill="#fff"/><path d="M1 1l8 6 8-6" stroke="#a40f16" fill="none"/></svg>Contact</div>
<div class="btn" style="left:976px;top:20px;width:111px;height:40px">
  <svg width="14" height="16" viewBox="0 0 14 16"><circle cx="7" cy="4" r="4" fill="#fff"/><path d="M0 16c0-5 3-7 7-7s7 2 7 7z" fill="#fff"/></svg>Login</div>
<nav class="abs main-nav"><span>Listings</span><span>Owners Prospect</span><span>Tenants</span><span>About</span><span>Community</span><span>Mortgage Info</span></nav>

<!-- hero -->
<div class="abs hero-photo" role="img" aria-label="Photo of a family walking into a bright new home, a child running ahead past a potted plant"></div>
<div class="abs hero-copy">
  <h1>CALL TODAY</h1>
  <p>Get 1 Month Property<br>Management Fee <em>Off.</em><br><em>$120</em> Value!!</p>
</div>
<div class="btn" style="left:114px;top:493px;width:112px;height:39px;border-radius:4px">Get Started</div>
<svg class="abs" style="left:0;top:690px" width="1200" height="160" viewBox="0 0 1200 160">
  <polygon points="0,13 877,110 1200,17 1200,160 0,160" fill="#fff"/>
  <polygon points="0,13 877,110 1200,17 1200,45 877,138 0,28" fill="#a40f16"/>
</svg>

<!-- about -->
<div class="section-title" style="top:870px">About Us</div>
<div class="abs about-text">
  <p>Our vision for Brighthold Property Management is to provide the best Property Management Services to the Sacramento and surrounding areas. I am focused on providing a more personalized service to you and your tenants. This means we are a one-stop-shop. You only deal with me, no middle guy, so no time is wasted.</p>
  <p>Brighthold Property Management is operated and owned by me Daniel Whitford I have over 10 years of experience in property management combined with real estate appraising and understand the importance of 'return on investment.</p>
</div>
<div class="btn" style="left:544px;top:1146px;width:112px;height:41px">Read More</div>

<!-- property manager -->
<svg class="abs manager" viewBox="0 0 1200 563" width="1200" height="563">
  <rect width="1200" height="563" fill="#1b1f2b"/>
  <rect width="1200" height="563" fill="url(#mgrShade)"/>
  <defs><linearGradient id="mgrShade" x1="0" x2="1"><stop offset="0" stop-color="#262a36"/><stop offset="1" stop-color="#3a2a2c"/></linearGradient></defs>
  <rect x="735" y="0" width="107" height="8" fill="#111"/>
  <rect x="735" y="555" width="107" height="8" fill="#111"/>
  <polygon points="735,10 1200,10 1200,553 735,553 602,282" fill="#fff"/>
  <polygon points="750,22 1200,22 1200,541 750,541 622,282" fill="#c9c2b0" role="img" aria-label="Photo of a two-storey house with a red For Rent sign on the front lawn"/>
</svg>
<div class="abs manager-copy">
  <h2><span class="dash"></span>Property Manager for Your Rental</h2>
  <p>Vacancy periods are significantly reduced with an extensive pool of prospective renters as well as free advertising.Save on repairs. I have negotiated with maintenance contractors and receive discounts that are passed on to you.</p>
  <p style="margin-top:12px">I perform extensive background checks on prospective renters to minimize your overall vacancy rate and potential non-payments of rent.Regular inspections on your property will be made, inside and out.</p>
</div>
<div class="btn" style="left:111px;top:1737px;width:112px;height:40px;border-radius:4px">Read More</div>

<!-- listings -->
<div class="section-title" style="top:1912px">Our Listings</div>
<div class="pager" style="left:44px"></div>
<div class="pager" style="left:1125px"></div>

<div class="card" style="left:110px">
  <div class="ph" role="img" aria-label="Photo of a single-storey rental with a large tree in the yard" style="background:linear-gradient(180deg,#6f9bd0,#9c8b76 55%,#8a6a55)"></div>
  <h3>Fantastic opportunity 2 Bdrm x 1 Bth ADU Unit!!</h3>
  <span class="price" style="top:306px">$2,000.00</span>
  <span class="status" style="left:203px;top:303px">Available</span>
  <div class="specs">
    <svg width="30" height="18" viewBox="0 0 30 18"><path d="M2 2v15M28 9v8M2 12h26M2 9h26v3M5 9V5h8v4" fill="none" stroke="#333" stroke-width="1.5"/></svg>2
    <svg width="30" height="20" viewBox="0 0 30 20" style="margin-left:22px"><path d="M2 9h26l-3 8H5zM6 9V3a2 2 0 014 0" fill="none" stroke="#333" stroke-width="1.5"/></svg>1
    <svg width="42" height="10" viewBox="0 0 42 10" style="margin-left:40px"><path d="M1 5h40M5 1L1 5l4 4M37 1l4 4-4 4" fill="none" stroke="#333" stroke-width="1.5"/></svg>693 Sq. Ft.
  </div>
</div>

<div class="card" style="left:440px">
  <div class="ph" role="img" aria-label="Photo of a white kitchen with a refrigerator" style="background:linear-gradient(180deg,#e9e7e3,#c8c3ba 70%,#8d7e70)"></div>
  <h3>1430 Maple St. #4</h3>
  <span class="price" style="top:285px">$1,695.00</span>
  <div class="specs">
    <svg width="30" height="18" viewBox="0 0 30 18"><path d="M2 2v15M28 9v8M2 12h26M2 9h26v3M5 9V5h8v4" fill="none" stroke="#333" stroke-width="1.5"/></svg>3
    <svg width="30" height="20" viewBox="0 0 30 20" style="margin-left:22px"><path d="M2 9h26l-3 8H5zM6 9V3a2 2 0 014 0" fill="none" stroke="#333" stroke-width="1.5"/></svg>1
    <svg width="42" height="10" viewBox="0 0 42 10" style="margin-left:40px"><path d="M1 5h40M5 1L1 5l4 4M37 1l4 4-4 4" fill="none" stroke="#333" stroke-width="1.5"/></svg>693 Sq. Ft.
  </div>
</div>
<div class="rented">Rented</div>

<div class="card" style="left:768px">
  <div class="ph" role="img" aria-label="Photo of a low ranch-style building among tall trees" style="background:linear-gradient(180deg,#3f7fd0 0%,#5f9ad8 40%,#4d6b3a 65%,#9b9c8e)"></div>
  <h3>5817 Linden Ave #3</h3>
  <span class="status" style="left:18px;top:298px">Available</span>
  <div class="specs" style="top:358px">
    <svg width="30" height="20" viewBox="0 0 30 20"><path d="M2 9h26l-3 8H5zM6 9V3a2 2 0 014 0" fill="none" stroke="#333" stroke-width="1.5"/></svg>1
    <svg width="42" height="10" viewBox="0 0 42 10" style="margin-left:40px"><path d="M1 5h40M5 1L1 5l4 4M37 1l4 4-4 4" fill="none" stroke="#333" stroke-width="1.5"/></svg>1,350 Sq. Ft.
  </div>
</div>

<!-- applicants -->
<div class="abs applicants" role="img" aria-label="Dusk photo of a modern two-storey house with lit windows"></div>
<div class="section-title light" style="top:2595px;line-height:52px;font-size:42px;align-items:flex-start"><span style="text-align:center">Rental Applicants and<br>Prospective Tenants</span></div>

<div class="feature" style="left:63px">
  <svg width="148" height="140" viewBox="0 0 148 140"><path d="M74 4L4 66h14v70h112V66h14z" fill="#fff"/><circle cx="72" cy="74" r="22" fill="#a40f16"/><text x="72" y="84" text-anchor="middle" font-size="28" fill="#fff" font-family="serif" font-weight="700">$</text><path d="M52 104l20-14 12 8 22-20" stroke="#a40f16" stroke-width="6" fill="none"/></svg>INCOME</div>
<div class="feature" style="left:282px">
  <svg width="148" height="140" viewBox="0 0 148 140"><path d="M74 4L4 66h14v70h112V66h14z" fill="#fff"/><rect x="48" y="56" width="40" height="50" rx="3" fill="#a40f16"/><rect x="54" y="64" width="14" height="10" fill="#fff"/><rect x="54" y="80" width="28" height="4" fill="#fff"/><rect x="54" y="90" width="28" height="4" fill="#fff"/><circle cx="92" cy="64" r="12" fill="#a40f16" stroke="#fff" stroke-width="3"/></svg>CREDIT REPORTS</div>
<div class="feature" style="left:502px">
  <svg width="148" height="140" viewBox="0 0 148 140"><path d="M74 4L4 66h14v70h112V66h14z" fill="#fff"/><circle cx="60" cy="66" r="8" fill="#a40f16"/><circle cx="88" cy="84" r="8" fill="#a40f16"/><path d="M46 92c0-10 28-10 28 0zM74 108c0-10 28-10 28 0z" fill="#a40f16"/><path d="M78 60h16v12M70 104H54V92" stroke="#a40f16" stroke-width="5" fill="none"/></svg>REFERENCES</div>
<div class="feature" style="left:721px">
  <svg width="148" height="140" viewBox="0 0 148 140"><path d="M74 4L4 66h14v70h112V66h14z" fill="#fff"/><ellipse cx="74" cy="92" rx="16" ry="13" fill="#a40f16"/><circle cx="58" cy="70" r="6" fill="#a40f16"/><circle cx="68" cy="62" r="6" fill="#a40f16"/><circle cx="80" cy="62" r="6" fill="#a40f16"/><circle cx="90" cy="70" r="6" fill="#a40f16"/></svg>PETS</div>
<div class="feature" style="left:940px;width:200px">
  <svg width="148" height="140" viewBox="0 0 148 140"><path d="M74 4L4 66h14v70h112V66h14z" fill="#fff"/><circle cx="74" cy="62" r="8" fill="#a40f16"/><path d="M62 82c0-10 24-10 24 0z" fill="#a40f16"/><circle cx="52" cy="100" r="7" fill="#a40f16"/><circle cx="74" cy="100" r="7" fill="#a40f16"/><circle cx="96" cy="100" r="10" fill="#a40f16"/><path d="M91 100l4 4 7-8" stroke="#fff" stroke-width="3" fill="none"/><path d="M52 92v-6h44v6M74 82v18" stroke="#a40f16" stroke-width="3" fill="none"/></svg>SELECTION PROCESS</div>
<div class="btn" style="left:545px;top:2992px;width:111px;height:41px">View All</div>

<!-- property information -->
<div class="section-title" style="top:3140px">Property Information</div>
<div class="field" style="left:110px;top:3243px;width:324px">Type Of Property<svg class="chev" width="12" height="8" viewBox="0 0 12 8"><path d="M1 1l5 5 5-5" stroke="#333" fill="none" stroke-width="1.5"/></svg></div>
<div class="field" style="left:440px;top:3243px;width:324px">Number Of Bedrooms</div>
<div class="field" style="left:770px;top:3243px;width:324px">Number Of Bathrooms</div>
<div class="field" style="left:110px;top:3305px;width:324px">Property Address</div>
<div class="field" style="left:440px;top:3305px;width:324px">City,State<svg class="chev" width="12" height="8" viewBox="0 0 12 8"><path d="M1 1l5 5 5-5" stroke="#333" fill="none" stroke-width="1.5"/></svg></div>
<div class="field" style="left:770px;top:3305px;width:324px">Postal Code</div>
<div class="field" style="left:110px;top:3367px;width:984px;height:122px">Message</div>
<div class="btn" style="left:544px;top:3507px;width:112px;height:40px">Submit</div>

<!-- footer -->
<svg class="abs footer-bg" viewBox="0 0 1200 434" width="1200" height="434">
  <polygon points="0,112 322,8 1200,120 1200,434 0,434" fill="#f1f1f1"/>
  <polygon points="0,112 322,8 1200,120 1200,124 322,26 0,130" fill="#a40f16"/>
</svg>
<div class="brand" style="left:480px;top:3712px;width:240px">
  <span class="brand-mark" style="width:48px;height:48px"></span>
  <span class="brand-name" style="font-size:31px;margin-top:22px">BRIGHTHOLD</span>
</div>
<div class="abs" style="left:512px;top:3856px;display:flex;gap:30px;align-items:center">
  <span style="width:28px;height:26px;background:#333;display:block"></span>
  <span style="width:60px;height:26px;background:#555;display:block"></span>
  <span style="width:26px;height:26px;background:#333;display:block"></span>
</div>
<div class="abs foot-links"><span>Listings</span><span>Owners</span><span>Prospect Tenants</span><span>About</span><span>Community</span><span>Mortgage Info</span></div>
<div class="abs" style="left:110px;top:3975px;width:976px;height:2px;background:#222"></div>
<div class="abs copyright">Copyright© 2024 BRIGHTHOLD PROPERTY MANAGEMENT INC.</div>
<div class="abs socials"><i></i><i></i><i></i><i></i><i></i><i></i></div>

</body>
</html>
```